Customer Value Leaflet

We need a bi-fold brochure designing, based on the attached PDF wireframes. Our company name is brambleharvik.com (of which the logo is currently being designed). The corporate colour is orange (the exact shade of which we are happy to leave to the designers discretion).

The leaflet will distributed to customer experience experts and marketers so the design needs to be bright, engaging, clean and simple. Design is critical.

It Company

```html
<!DOCTYPE html>
<html lang="en">
<head>
<meta charset="utf-8">
<title>Customer Value Leaflet</title>
<link href="https://fonts.googleapis.com/css2?family=Arimo:wght@400;700&family=Amatic+SC:wght@400;700&display=swap" rel="stylesheet">
<style>
:root{
  --orange:#f07f3c;
  --orange-light:#f6b48a;
  --blue:#3a9fd4;
  --blue-light:#9dcde4;
  --blue-mid:#7fb9dd;
  --stage:#e4e4e4;
  --paper:#ffffff;
  --fold:#e6e6e6;
  --ink:#333333;
  --grey:#c9c9c9;
}
*{box-sizing:border-box;margin:0;padding:0}
html,body{width:1200px;height:741px;overflow:hidden}
body{background:var(--stage);font-family:"Arimo",Arial,sans-serif;position:relative}
.spread{position:absolute;left:30px;width:1140px;height:345px;display:flex;background:var(--paper);box-shadow:0 2px 8px rgba(0,0,0,.12)}
.spread--inside{top:18px}
.spread--outside{top:380px}
.panel{position:relative;width:380px;height:345px;overflow:hidden}
.panel+.panel{border-left:1px solid var(--fold)}
.abs{position:absolute}
.art{position:absolute;background:radial-gradient(circle,#f3d9c6,#e9a77a)}
.art--round{border-radius:50%}
.art--bag{background:var(--orange)}
.art--cart{background:linear-gradient(#fff,#fbe3d3);border:2px solid var(--orange);border-radius:6px}
.art--hand{background:var(--orange);border-radius:40%}

.pill-head{left:0;top:14px;width:300px;height:36px;background:var(--orange);border-radius:0 18px 18px 0;color:#fff;font-size:18px;line-height:36px;text-align:center}
.char-name{font-family:"Amatic SC",cursive;font-size:26px;letter-spacing:4px;color:var(--ink)}
.clv{font-size:20px;font-weight:700;color:var(--orange)}
.clv-note{font-size:11.5px;line-height:13px;color:var(--orange);text-align:center;width:135px}
.blue-copy{left:10px;top:252px;width:360px;text-align:center;color:var(--blue);font-size:12.5px;font-weight:700;line-height:15px}
.band{height:38px;border-radius:19px;color:#fff;text-align:center;font-weight:700}
.band--blue{background:var(--blue)}
.band--orange{background:var(--orange)}
.url-band{left:-20px;top:298px;width:380px;line-height:38px;font-size:19px}

.step{font-size:12px;line-height:14px;color:var(--ink);text-align:center}
.tweet-box{left:332px;top:94px;width:32px;height:32px;background:var(--blue);border-radius:6px}

.blob{left:14px;width:352px;border-radius:60px;color:#fff;font-family:"Amatic SC",cursive;font-size:34px;line-height:34px;text-align:center;display:flex;align-items:center;justify-content:center;padding:0 20px}
.blob--blue{top:22px;height:130px;background:var(--blue-light)}
.blob--orange{top:140px;height:135px;background:var(--orange)}
.more-band{left:14px;top:290px;width:380px;height:50px;border-radius:25px 0 0 25px;background:var(--blue);color:#fff;text-align:center;font-size:15px;line-height:19px;padding-top:6px}
.more-band b{font-size:16px}

.bubble{color:#fff;font-size:11.5px;line-height:14px;padding:10px 18px}
.bubble--orange{left:45px;top:14px;width:215px;background:var(--orange);border-radius:30px}
.bubble--blue{left:15px;top:190px;width:350px;background:var(--blue);border-radius:40px;font-size:14px;line-height:17px;padding:14px 24px}
.bubble b{font-weight:700}
.pies{left:20px;top:98px;width:340px;display:flex;justify-content:space-between}

.logo-box{left:128px;top:14px;width:100px;height:50px;background:var(--orange);color:#fff;font-size:22px;font-weight:700;line-height:50px;text-align:center}
.cover-line{left:0;width:380px;text-align:center;color:var(--ink);font-size:30px;line-height:36px}
.cover-bar{left:170px;top:262px;width:120px;height:83px;background:var(--orange)}
</style>
</head>
<body>

<section class="spread spread--inside">
  <div class="panel panel--clv">
    <div class="abs pill-head">Once you can calculate CLV</div>
    <div class="art art--round" style="left:22px;top:66px;width:80px;height:80px" role="img" aria-label="Illustration of Kim, a customer with glasses and a bun"></div>
    <div class="abs char-name" style="left:104px;top:62px">Kim</div>
    <svg class="abs" style="left:150px;top:50px" width="50" height="200" viewBox="0 0 50 200">
      <path d="M12 0 H38 V165 H50 L25 200 L0 165 H12 Z" fill="var(--blue)"/>
      <text x="31" y="10" transform="rotate(90 31 10)" font-family="Arimo, sans-serif" font-size="13" fill="#fff">optimise your marketing</text>
    </svg>
    <div class="abs char-name" style="left:208px;top:62px">Kevin</div>
    <div class="art art--round" style="left:285px;top:62px;width:84px;height:84px" role="img" aria-label="Illustration of Kevin, a customer with spiky hair"></div>
    <div class="abs clv" style="left:20px;top:162px">CLV of £149</div>
    <div class="abs clv-note" style="left:18px;top:188px">You can personalize Kim's marketing experience to grow her lifetime value to be more like Kevin's</div>
    <div class="abs clv" style="left:215px;top:162px">CLV of £282</div>
    <div class="abs clv-note" style="left:212px;top:188px">You can understand why Kevin is more valuable and acquire more customers like him</div>
    <p class="abs blue-copy">We use data and science to predict how your customers will behave in the future. Even if you already use CLV, we can help you do and earn more.</p>
    <div class="abs band band--blue url-band">www.brambleharvik.com</div>
  </div>

  <div class="panel panel--timeline">
    <div class="art art--round" style="left:22px;top:12px;width:62px;height:62px" role="img" aria-label="Illustration of Kim"></div>
    <svg class="abs" style="left:172px;top:10px" width="40" height="305" viewBox="0 0 40 305">
      <path d="M6 0 H34 V265 H40 L20 300 L0 265 H6 Z" fill="var(--blue)"/>
      <text transform="translate(25 85) rotate(-90)" font-family="Arimo, sans-serif" font-size="14" fill="#fff">+1 week</text>
      <text transform="translate(25 175) rotate(-90)" font-family="Arimo, sans-serif" font-size="14" fill="#fff">+1 month</text>
      <text transform="translate(25 265) rotate(-90)" font-family="Arimo, sans-serif" font-size="14" fill="#fff">+6 months</text>
    </svg>
    <p class="abs step" style="left:8px;top:80px;width:140px">Kim calls you to return an item...</p>
    <div class="art art--cart" style="left:35px;top:114px;width:95px;height:62px" role="img" aria-label="Shopping trolley illustration"></div>
    <p class="abs step" style="left:45px;top:126px;width:80px">places 4 more online orders</p>
    <p class="abs step" style="left:5px;top:192px;width:160px">then places another order but then doesn't come back for a month</p>
    <div class="art art--hand" style="left:50px;top:250px;width:38px;height:40px" role="img" aria-label="Waving hand illustration"></div>

    <div class="art art--bag" style="left:220px;top:14px;width:40px;height:46px" role="img" aria-label="Shopping bag illustration"></div>
    <div class="art art--round" style="left:268px;top:6px;width:64px;height:64px" role="img" aria-label="Illustration of Kevin"></div>
    <p class="abs step" style="left:218px;top:82px;width:115px">Kevin makes another purchase...</p>
    <div class="abs tweet-box"></div>
    <p class="abs step" style="left:218px;top:128px;width:150px">then 2 more (and even tweets about how great your service is)...</p>
    <div class="art art--cart" style="left:235px;top:182px;width:120px;height:90px" role="img" aria-label="Shopping trolley illustration"></div>
    <p class="abs step" style="left:245px;top:196px;width:100px">and continues to make purchases on a bi-monthly basis</p>
    <div class="abs band band--orange" style="left:20px;top:300px;width:340px;line-height:38px;font-size:17px;font-weight:400">But really it is <b>Kevin.</b></div>
  </div>

  <div class="panel panel--closing">
    <div class="abs blob blob--blue">By predicting customer lifetime value today...</div>
    <div class="abs blob blob--orange">...you can optimise your business for tomorrow.</div>
    <div class="abs more-band">Find out more on<br><b>www.brambleharvik.com</b></div>
  </div>
</section>

<section class="spread spread--outside">
  <div class="panel panel--clv">
    <div class="abs pill-head">Once you can calculate CLV</div>
    <div class="art art--round" style="left:22px;top:66px;width:80px;height:80px" role="img" aria-label="Illustration of Kim, a customer with glasses and a bun"></div>
    <div class="abs char-name" style="left:104px;top:62px">Kim</div>
    <svg class="abs" style="left:150px;top:50px" width="50" height="200" viewBox="0 0 50 200">
      <path d="M12 0 H38 V165 H50 L25 200 L0 165 H12 Z" fill="var(--blue)"/>
      <text x="31" y="10" transform="rotate(90 31 10)" font-family="Arimo, sans-serif" font-size="13" fill="#fff">optimise your marketing</text>
    </svg>
    <div class="abs char-name" style="left:208px;top:62px">Kevin</div>
    <div class="art art--round" style="left:285px;top:62px;width:84px;height:84px" role="img" aria-label="Illustration of Kevin, a customer with spiky hair"></div>
    <div class="abs clv" style="left:20px;top:162px">CLV of £149</div>
    <div class="abs clv-note" style="left:18px;top:188px">You can personalize Kim's marketing experience to grow her lifetime value to be more like Kevin's</div>
    <div class="abs clv" style="left:215px;top:162px">CLV of £282</div>
    <div class="abs clv-note" style="left:212px;top:188px">You can understand why Kevin is more valuable and acquire more customers like him</div>
    <p class="abs blue-copy">We use data and science to predict how your customers will behave in the future. Even if you already use CLV, we can help you do and earn more.</p>
    <div class="abs band band--blue url-band">www.brambleharvik.com</div>
  </div>

  <div class="panel panel--platform">
    <p class="abs bubble bubble--orange"><b>ORBITA</b> is our Customer Value Platform, designed for Marketers in the Digital Enterprise.</p>
    <div class="abs pies">
      <svg width="90" height="90" viewBox="0 0 90 90" role="img" aria-label="Pie chart">
        <circle cx="45" cy="45" r="40" fill="var(--orange-light)"/>
        <path d="M45 45 L45 5 A40 40 0 0 1 79.6 65 Z" fill="var(--orange)"/>
      </svg>
      <svg width="90" height="90" viewBox="0 0 90 90" role="img" aria-label="Pie chart">
        <circle cx="45" cy="45" r="40" fill="var(--blue-light)"/>
        <path d="M45 45 L45 5 A40 40 0 0 1 45 85 Z" fill="var(--blue)"/>
        <path d="M45 45 L45 85 A40 40 0 0 1 7.4 58.7 Z" fill="var(--blue-mid)"/>
      </svg>
      <svg width="90" height="90" viewBox="0 0 90 90" role="img" aria-label="Pie chart">
        <circle cx="45" cy="45" r="40" fill="var(--ink)"/>
        <path d="M45 45 L5 45 A40 40 0 0 1 45 5 Z" fill="var(--grey)"/>
        <path d="M45 45 L45 5 A40 40 0 0 1 65 10.4 Z" fill="#fff"/>
      </svg>
    </div>
    <p class="abs bubble bubble--blue"><b>ORBITA</b> is like having a team of <b>data scientists</b> making valuable insights available to your website in real-time so that you can deliver <b>the ultimate customer experience</b></p>
  </div>

  <div class="panel panel--cover">
    <div class="abs logo-box">Logo</div>
    <div class="abs cover-line" style="top:80px">We're a</div>
    <div class="abs cover-line" style="top:124px">Customer Value</div>
    <div class="abs cover-line" style="top:168px">Company</div>
    <div class="abs cover-bar"></div>
  </div>
</section>

</body>
</html>
```